Banner for construction site to identify developer

we need a 4 foot by 8 foot banner to hang on the fence of a residential townhome development in Phoenix, Arizona that identifies Tolvane Holdings as the company behind the development/project. Also needs to include the logo, phone number, and web address. Would like to stick with the blue colors provided in the attached logo. The blues should stay the same but the letters in the logo can change to another color if necessary. Feel free to use "Tolvane Holdings" in place of "Tolvane Holdings Group". Looking for use of colors/design to take up space so banner is not just text with a logo.

Target Market(s)

drive by traffic looking at the site

Industry/Entity Type

Real Estate

Colors
0054AA
0677BA
7BADD7
CADEEF
E8F1F8

Requirements
Must have
• company name, phone number and web address

```html
<!DOCTYPE html>
<html lang="en">
<head>
<meta charset="utf-8">
<title>Tolvane Holdings – Site Banner</title>
<link rel="stylesheet" href="https://fonts.googleapis.com/css2?family=Open+Sans:wght@600;700;800&display=swap">
<style>
  :root {
    --backdrop: #a9a9a9;
    --banner-white: #ffffff;
    --brand-sky: #1fa8d9;
    --brand-blue: #1f6fa0;
    --charcoal: #414042;
    --name-ink: #3c3c3e;
    --white: #ffffff;
  }
  * { box-sizing: border-box; margin: 0; padding: 0; }
  html, body {
    width: 921px;
    height: 1200px;
    overflow: hidden;
    background: var(--backdrop);
    font-family: "Open Sans", Arial, sans-serif;
  }
  .banner {
    position: absolute;
    left: 50px;
    top: 395px;
    width: 821px;
    height: 410px;
    background: var(--banner-white);
    box-shadow: 0 6px 14px rgba(0,0,0,0.35);
    display: flex;
    flex-direction: column;
  }
  .banner__identity {
    height: 238px;
    display: flex;
    align-items: center;
    justify-content: center;
    gap: 22px;
    padding-top: 20px;
  }
  .identity__mark {
    width: 64px;
    height: 64px;
    background: var(--brand-sky);
  }
  .identity__name {
    font-weight: 700;
    font-size: 68px;
    letter-spacing: -1.5px;
    color: var(--name-ink);
    line-height: 1;
  }
  .banner__footer {
    flex: 1;
    display: flex;
  }
  .footer__tagline {
    width: 403px;
    background: var(--brand-blue);
    color: var(--white);
    font-weight: 700;
    font-size: 26px;
    line-height: 1.17;
    text-transform: uppercase;
    padding: 30px 0 0 35px;
  }
  .footer__contact {
    flex: 1;
    background: var(--charcoal);
    color: var(--white);
    padding: 30px 0 0 18px;
  }
  .contact__phone {
    display: flex;
    align-items: center;
    gap: 10px;
    font-weight: 600;
    font-size: 40px;
    line-height: 1;
  }
  .contact__icon { width: 32px; height: 32px; flex: none; }
  .contact__web {
    margin-top: 14px;
    font-weight: 600;
    font-size: 24.5px;
    line-height: 1;
  }
</style>
</head>
<body>
  <main class="banner">
    <header class="banner__identity">
      <span class="identity__mark" aria-hidden="true"></span>
      <h1 class="identity__name">Tolvane Holdings</h1>
    </header>
    <section class="banner__footer">
      <p class="footer__tagline">Crafting Phoenix's<br>Premium Residential<br>Townhomes</p>
      <div class="footer__contact">
        <p class="contact__phone">
          <svg class="contact__icon" viewBox="0 0 32 32" aria-hidden="true">
            <circle cx="16" cy="16" r="16" fill="var(--brand-sky)"/>
            <path d="M11.2 8.5c.6-.4 1.4-.3 1.8.3l1.8 2.7c.4.6.3 1.3-.2 1.7l-1.2 1c.8 1.9 2.3 3.4 4.2 4.3l1-1.2c.4-.5 1.2-.6 1.7-.2l2.7 1.8c.6.4.7 1.2.3 1.8l-1 1.4c-.6.8-1.6 1.2-2.6.9-4.6-1.3-8.2-4.9-9.5-9.5-.3-1 .1-2 .9-2.6z" fill="var(--charcoal)"/>
          </svg>
          (480) 555-0147
        </p>
        <p class="contact__web">www.tolvaneholdings.com</p>
      </div>
    </section>
  </main>
</body>
</html>
```